RWT Fittings Ltd Business Cards

We need a business card with our business logo. We provide window and door installations on high-rises in west coast British Colombia, Canada.

I would like my business information and details on one side of the card, and the other side the company name with logo

Target Market(s)

General Contractors

Industry/Entity Type

Construction

Contact Information for Business Card

one side i want my company name and logo in the dark theme logo that i provided

Requirements
Must have
• Marco Peltieri, 16045518293, RWTFittings@mailbox-demo.com, 1407-5194 Linden Row Burnaby BC, V5H 2K9, Owner & Manager

```html
<!DOCTYPE html>
<html lang="en">
<head>
<meta charset="utf-8">
<title>RWT Fittings Ltd – Business Cards</title>
<link rel="stylesheet" href="https://fonts.googleapis.com/css2?family=Open+Sans:wght@400;700&display=swap">
<style>
  :root {
    --page: #2c2c2c;
    --card: #1b1b1c;
    --blue: #29a9e1;
    --blue-deep: #2e98cc;
    --grey: #8f8f8f;
    --white: #f2f2f2;
  }
  * { margin: 0; padding: 0; box-sizing: border-box; }
  html, body { width: 1200px; height: 780px; overflow: hidden; }
  body {
    background: var(--page);
    font-family: "Open Sans", Arial, sans-serif;
    display: flex;
    align-items: center;
    justify-content: center;
    gap: 40px;
  }
  .card {
    position: relative;
    width: 540px;
    height: 309px;
    background: var(--card);
    overflow: hidden;
  }

  /* Logo stand-in: name + plain square */
  .brand {
    display: flex;
    align-items: center;
    gap: 12px;
  }
  .brand-square {
    width: 22px;
    height: 22px;
    background: var(--grey);
    flex: none;
  }
  .brand-name {
    color: var(--blue);
    font-weight: 700;
    white-space: nowrap;
    letter-spacing: 0.5px;
  }

  /* Contact side */
  .card-contact .brand {
    position: absolute;
    left: 34px;
    top: 104px;
  }
  .card-contact .brand-name { font-size: 21px; }
  .card-contact .brand-square { width: 18px; height: 18px; }

  .divider {
    position: absolute;
    left: 272px;
    top: 40px;
    width: 1px;
    height: 200px;
    background: var(--blue);
  }
  .details {
    position: absolute;
    left: 292px;
    top: 48px;
    width: 236px;
    color: var(--white);
    font-size: 12.5px;
    line-height: 1.45;
  }
  .person-name {
    color: var(--blue);
    font-weight: 700;
    font-size: 19px;
    text-transform: uppercase;
    line-height: 1.2;
  }
  .person-role { font-size: 13.5px; margin-bottom: 8px; }
  .contact-list { list-style: none; }
  .contact-item {
    display: flex;
    align-items: flex-start;
    gap: 6px;
    margin-bottom: 2px;
  }
  .contact-item svg { flex: none; margin-top: 3px; }
  .address { margin-top: 4px; }

  .edge-band {
    position: absolute;
    left: 0;
    bottom: 0;
    width: 540px;
    height: 26px;
  }

  /* Name side */
  .card-name {
    display: flex;
    align-items: center;
    justify-content: center;
  }
  .card-name .brand { gap: 16px; }
  .card-name .brand-name { font-size: 40px; }
  .card-name .brand-square { width: 34px; height: 34px; }
</style>
</head>
<body>

  <section class="card card-contact" aria-label="Business card, contact side">
    <div class="brand">
      <span class="brand-square"></span>
      <span class="brand-name">RWT Fittings Ltd</span>
    </div>

    <span class="divider"></span>

    <div class="details">
      <p class="person-name">Marco Peltieri</p>
      <p class="person-role">Owner &amp; Manager</p>
      <ul class="contact-list">
        <li class="contact-item">
          <svg width="11" height="11" viewBox="0 0 24 24" aria-hidden="true"><path fill="#29a9e1" d="M6.6 10.8a15 15 0 0 0 6.6 6.6l2.2-2.2c.3-.3.7-.4 1-.2 1.1.4 2.3.6 3.6.6.6 0 1 .4 1 1V20c0 .6-.4 1-1 1A17 17 0 0 1 3 4c0-.6.4-1 1-1h3.5c.6 0 1 .4 1 1 0 1.3.2 2.5.6 3.6.1.3 0 .7-.2 1z"/></svg>
          <span>16045518293</span>
        </li>
        <li class="contact-item">
          <svg width="11" height="11" viewBox="0 0 24 24" aria-hidden="true"><path fill="#29a9e1" d="M2 5h20v14H2z"/><path fill="none" stroke="#1b1b1c" stroke-width="2" d="M2 5l10 8 10-8"/></svg>
          <span>RWTFittings@mailbox-demo.com</span>
        </li>
        <li class="contact-item">
          <svg width="11" height="11" viewBox="0 0 24 24" aria-hidden="true"><circle cx="12" cy="12" r="10" fill="none" stroke="#29a9e1" stroke-width="2.5"/><path fill="none" stroke="#29a9e1" stroke-width="2" d="M2 12h20M12 2c3 3 3 17 0 20M12 2c-3 3-3 17 0 20"/></svg>
          <span>www.rwtfittings-demo.com</span>
        </li>
        <li class="contact-item address">
          <svg width="11" height="11" viewBox="0 0 24 24" aria-hidden="true"><path fill="#29a9e1" d="M12 2a7 7 0 0 0-7 7c0 5 7 13 7 13s7-8 7-13a7 7 0 0 0-7-7zm0 9.5A2.5 2.5 0 1 1 12 6.5a2.5 2.5 0 0 1 0 5z"/></svg>
          <span>1407-5194 Linden Row<br>Burnaby BC, V5H 2K9</span>
        </li>
      </ul>
    </div>

    <svg class="edge-band" viewBox="0 0 540 26" aria-hidden="true">
      <path fill="#8f8f8f" d="M0 0H196L206 12H0z"/>
      <path fill="#2e98cc" d="M190 26C196 18 204 14 216 14H540V26z"/>
    </svg>
  </section>

  <section class="card card-name" aria-label="Business card, company side">
    <div class="brand">
      <span class="brand-square"></span>
      <span class="brand-name">RWT Fittings Ltd</span>
    </div>
  </section>

</body>
</html>
```